Marwick Family Chiropractic Stationary

The letterhead and business card must have our logo.
We would like to see the logo used in different ways ( It can be expanded upon in the stationary.)
Please use the the same or similar colors.
Must be eye catching and memorable.
Must be easy to read

Reason: The doctor has been too busy to make any final decisions. He would like to give himself a little more time.

Target Market(s)

Chiropractic Healthcare

Industry/Entity Type

Business

Requirements
Must have
• Dr. Leonard Marwick D.C.
Chiropractor

860-555-0183

417 Birchfield Road, 2nd Floor
Hollisfield 06091

drmarwick@marwickspine.example
www.marwickspine.example
www.facebook.com/MarwickFamilySpine
Should not have
• should not be difficult to read

```html
<!DOCTYPE html>
<html lang="en">
<head>
<meta charset="utf-8">
<title>Marwick Family Chiropractic – Business Cards</title>
<link rel="stylesheet" href="https://fonts.googleapis.com/css2?family=Montserrat:wght@600;700&family=Source+Sans+3:wght@400;600;700&display=swap">
<style>
  :root {
    --stage: #bdbdbd;
    --ink-black: #000000;
    --leaf-light: #a6cf5a;
    --leaf-deep: #289845;
    --bark-grey: #8c8279;
    --mist-grey: #c9c4bd;
    --text-dark: #3b3b3b;
    --paper-white: #ffffff;
    --card-w: 556px;
    --card-h: 317px;
  }
  * { margin: 0; padding: 0; box-sizing: border-box; }
  html, body {
    width: 1200px; height: 740px; overflow: hidden;
    background: var(--stage);
    font-family: "Source Sans 3", "Helvetica Neue", Arial, sans-serif;
  }
  .sheet { position: relative; width: 1200px; height: 740px; }

  .card {
    position: absolute; width: var(--card-w); height: var(--card-h);
    overflow: hidden;
  }
  .card--front { left: 28px; top: 30px; background: var(--ink-black); }
  .card--back-dark { left: 613px; top: 30px; background: var(--ink-black); }
  .card--back-deep { left: 28px; top: 385px; background: var(--leaf-deep); }
  .card--back-light { left: 613px; top: 385px; background: var(--leaf-light); }

  /* brand mark: name set in one colour, one weight, with a plain circle */
  .brand { position: absolute; left: 0; right: 0; text-align: center; }
  .brand__dot { display: block; margin: 0 auto; border-radius: 50%; }
  .brand__name {
    display: block; font-family: "Source Sans 3", Arial, sans-serif;
    font-weight: 700; letter-spacing: 1px; line-height: 1.05;
  }

  .card--front .brand { top: 28px; }
  .card--front .brand__dot { width: 70px; height: 70px; background: var(--leaf-light); margin-bottom: 16px; }
  .card--front .brand__name--main { color: var(--leaf-light); font-size: 33px; letter-spacing: 1.5px; }
  .card--front .brand__name--sub { color: var(--mist-grey); font-size: 13px; letter-spacing: 1.3px; margin-top: 2px; }

  .contact-band {
    position: absolute; left: 0; right: 0; bottom: 0; height: 103px;
    background: var(--leaf-light);
    border-top: 3px solid var(--leaf-deep);
    color: var(--text-dark);
  }
  .contact-band__person {
    position: absolute; right: 294px; top: 9px; text-align: right;
    font-size: 14px; line-height: 20px;
  }
  .contact-band__name { font-weight: 700; font-size: 15.5px; letter-spacing: -0.2px; }
  .contact-band__role { margin-bottom: 4px; }
  .contact-band__divider {
    position: absolute; left: 277px; top: 12px; width: 1px; height: 78px;
    background: var(--text-dark);
  }
  .contact-list {
    position: absolute; left: 289px; top: 10px; list-style: none;
    font-size: 14px; line-height: 20.5px;
  }
  .contact-list li { display: flex; align-items: center; gap: 7px; white-space: nowrap; }
  .contact-list svg { width: 10px; height: 10px; flex: none; fill: var(--text-dark); }
  .contact-list .plain-square { width: 10px; height: 10px; background: var(--text-dark); flex: none; }

  .card--back-dark .brand { top: 82px; }
  .card--back-dark .brand__name { font-family: "Montserrat", Arial, sans-serif; }
  .card--back-dark .brand__name--main { color: var(--leaf-light); font-size: 68px; letter-spacing: 2px; }
  .card--back-dark .brand__name--sub { color: var(--bark-grey); font-size: 27px; letter-spacing: 2px; margin-top: 4px; }

  .web-line {
    position: absolute; left: 0; right: 0; bottom: 22px; text-align: center;
    color: var(--paper-white); font-size: 15px; letter-spacing: 2.6px;
  }

  .card--back-deep .brand, .card--back-light .brand { top: 44px; }
  .card--back-deep .brand__dot, .card--back-light .brand__dot {
    width: 160px; height: 160px; background: var(--paper-white); margin-bottom: 14px;
  }
  .card--back-deep .brand__name, .card--back-light .brand__name {
    color: var(--paper-white); font-size: 30px; letter-spacing: 4px;
  }
</style>
</head>
<body>
<main class="sheet">

  <section class="card card--front" aria-label="Business card front">
    <div class="brand">
      <span class="brand__dot"></span>
      <span class="brand__name brand__name--main">MARWICK</span>
      <span class="brand__name brand__name--sub">FAMILY CHIROPRACTIC</span>
    </div>
    <div class="contact-band">
      <div class="contact-band__person">
        <p class="contact-band__name">Dr. Leonard Marwick D.C.</p>
        <p class="contact-band__role">Chiropractor</p>
        <p>417 Birchfield Road</p>
        <p>Suite 4, Hollisfield 06091</p>
      </div>
      <span class="contact-band__divider"></span>
      <ul class="contact-list">
        <li><svg viewBox="0 0 10 10" aria-hidden="true"><path d="M2 0.5 3.6 0 4.4 2.6 3.2 3.4Q4 5.6 6.6 6.8L7.4 5.6 10 6.4 9.5 8Q8.6 10 6 9 1.6 7 0.5 3 0 1.4 2 0.5Z"/></svg>860-555-0183</li>
        <li><svg viewBox="0 0 10 10" aria-hidden="true"><path d="M0.5 2.5h9L5 5.6z"/><path d="M0.5 3.4 5 6.4 9.5 3.4V7.6H0.5z"/></svg>drmarwick@marwickspine.example</li>
        <li><svg viewBox="0 0 10 10" aria-hidden="true"><circle cx="5" cy="5" r="4.4" fill="none" stroke="#3b3b3b" stroke-width="1"/><ellipse cx="5" cy="5" rx="1.8" ry="4.4" fill="none" stroke="#3b3b3b" stroke-width="0.8"/><path d="M0.6 5h8.8" stroke="#3b3b3b" stroke-width="0.8"/></svg>www.marwickspine.example</li>
        <li><span class="plain-square"></span>MarwickFamilySpine</li>
      </ul>
    </div>
  </section>

  <section class="card card--back-dark" aria-label="Business card back, black">
    <div class="brand">
      <span class="brand__name brand__name--main">MARWICK</span>
      <span class="brand__name brand__name--sub">FAMILY CHIROPRACTIC</span>
    </div>
    <p class="web-line">www.marwickspine.example</p>
  </section>

  <section class="card card--back-deep" aria-label="Business card back, deep green">
    <div class="brand">
      <span class="brand__dot"></span>
      <span class="brand__name">MARWICK</span>
    </div>
    <p class="web-line">www.marwickspine.example</p>
  </section>

  <section class="card card--back-light" aria-label="Business card back, light green">
    <div class="brand">
      <span class="brand__dot"></span>
      <span class="brand__name">MARWICK</span>
    </div>
    <p class="web-line">www.marwickspine.example</p>
  </section>

</main>
</body>
</html>
```